Verdant Systems Business Card

want the back of card to be blue- with the logo in the center
front of card- info plus logo (info being mailing address, email address, and website address )
4 different names with titles to have on cards
1) Calvin Borsted - Owner
2) Naomi Trelvik- Customer Relationship Specialist
3) Felix Andrade- Vice President of Sales
4) Owen Markby- Chief Technology Officer

Target Market(s)

tech company in the government/probation office industry

Industry/Entity Type

Government Office

Contact Information for Business Card

1) Calvin Borsted - Owner

Colors
0355a3
ffffff

Requirements
Must have
• back side should be blue, with the logo placed in the center
• front side needs to include both the logo, as well as company info (info should include website address, email address, and mailing address)

```html
<!DOCTYPE html>
<html lang="en">
<head>
<meta charset="utf-8">
<title>Verdant Systems Business Card</title>
<link rel="stylesheet" href="https://fonts.googleapis.com/css2?family=EB+Garamond:wght@600&family=Roboto:wght@400&family=Open+Sans:wght@500&display=swap">
<style>
  :root {
    --page-bg: #e9e7e4;
    --card-front: #1a1b1d;
    --card-back: #172a52;
    --ink-light: #ffffff;
    --ink-soft: #f2f2f2;
    --divider: rgba(255, 255, 255, 0.55);
  }
  html, body {
    margin: 0;
    padding: 0;
    width: 1125px;
    height: 1200px;
    overflow: hidden;
    background: var(--page-bg);
  }
  .canvas {
    position: relative;
    width: 1125px;
    height: 1200px;
  }
  .card {
    position: absolute;
    left: 171px;
    width: 826px;
    height: 472px;
    box-shadow: 0 3px 8px rgba(0, 0, 0, 0.35);
  }
  .card--front { top: 106px; background: var(--card-front); }
  .card--back  { top: 639px; background: var(--card-back); }

  .holder {
    position: absolute;
    right: calc(826px - 340px);
    top: 196px;
    text-align: right;
    color: var(--ink-light);
  }
  .holder__name {
    font-family: "EB Garamond", serif;
    font-weight: 600;
    font-size: 35px;
    line-height: 1;
    margin: 0;
  }
  .holder__title {
    font-family: "Open Sans", sans-serif;
    font-weight: 500;
    font-size: 19px;
    margin-top: 8px;
  }
  .divider {
    position: absolute;
    left: 369px;
    top: 160px;
    width: 2px;
    height: 145px;
    background: linear-gradient(to bottom, transparent, var(--divider) 30%, var(--divider) 70%, transparent);
  }
  .contact-list {
    position: absolute;
    left: 398px;
    top: 178px;
    margin: 0;
    padding: 0;
    list-style: none;
    font-family: "Roboto", sans-serif;
    font-size: 20px;
    color: var(--ink-soft);
  }
  .contact-list li {
    display: flex;
    align-items: center;
    height: 26.3px;
  }
  .contact-list svg {
    width: 18px;
    height: 18px;
    margin-right: 12px;
    fill: var(--ink-light);
    flex: none;
  }

  .brand-name {
    position: absolute;
    left: 0;
    right: 0;
    top: 210px;
    text-align: center;
    font-family: "EB Garamond", serif;
    font-weight: 600;
    font-size: 60px;
    color: var(--ink-light);
    margin: 0;
  }
  .back-url {
    position: absolute;
    left: 0;
    right: 0;
    top: 400px;
    text-align: center;
    font-family: "Roboto", sans-serif;
    font-size: 20px;
    letter-spacing: 3px;
    color: var(--ink-light);
  }
</style>
</head>
<body>
<main class="canvas">
  <section class="card card--front">
    <div class="holder">
      <h1 class="holder__name">Calvin Borsted</h1>
      <div class="holder__title">Owner</div>
    </div>
    <div class="divider"></div>
    <ul class="contact-list">
      <li>
        <svg viewBox="0 0 24 24" aria-hidden="true"><path d="M6.6 10.8a15.1 15.1 0 0 0 6.6 6.6l2.2-2.2c.3-.3.7-.4 1-.2 1.1.4 2.3.6 3.6.6.6 0 1 .4 1 1V20c0 .6-.4 1-1 1C10.6 21 3 13.4 3 4c0-.6.4-1 1-1h3.5c.6 0 1 .4 1 1 0 1.3.2 2.5.6 3.6.1.3 0 .7-.2 1z"/></svg>
        555-218-4403
      </li>
      <li>
        <svg viewBox="0 0 24 24" aria-hidden="true"><path d="M7 1h10a2 2 0 0 1 2 2v18a2 2 0 0 1-2 2H7a2 2 0 0 1-2-2V3a2 2 0 0 1 2-2zm0 3v14h10V4zm5 15.5a1 1 0 1 0 0 2 1 1 0 0 0 0-2z"/></svg>
        555-730-1962
      </li>
      <li>
        <svg viewBox="0 0 24 24" aria-hidden="true"><path d="M2 5h20v14H2zm2 2v.5l8 5 8-5V7zm0 2.8V17h16V9.8l-8 5z"/></svg>
        info@verdantsystems.com
      </li>
      <li>
        <svg viewBox="0 0 24 24" aria-hidden="true"><path d="M12 2a10 10 0 1 0 0 20 10 10 0 0 0 0-20zm-1 17.9A8 8 0 0 1 4.2 10.2L9 15v1a2 2 0 0 0 2 2zm6.9-2.5A2 2 0 0 0 16 16h-1v-3a1 1 0 0 0-1-1H8v-2h2a1 1 0 0 0 1-1V7h2a2 2 0 0 0 2-2v-.4a8 8 0 0 1 2.9 12.8z"/></svg>
        www.verdantsystems.com
      </li>
    </ul>
  </section>

  <section class="card card--back">
    <h2 class="brand-name">Verdant Systems</h2>
    <div class="back-url">www.verdantsystems.com</div>
  </section>
</main>
</body>
</html>
```